2020 Teamwear Price List

Price list of our popular teamwear items that we wholesale to clubs and schools.
looking to create a price list with images, images can be obtained from our website:
www.corvelathletichub.com.au
price list does not have to have lots of details about each product, just a from price. with minimum order etc.
and we can email or post to our clients, so it can be A4 pages/booklet style.
i can also provide images after i choose the design layout we like, so you can just use generic images for now if required.
Updates

Target Market(s)

Clubs and Schools

Font styles to use
Sans Serif

Colors

Designer to choose colors to be used in the design.

Requirements
Must have
• Photo or generated image for each product.
Nice to have
• simple format , easy to read , and easy to update from time to time

```html
<!DOCTYPE html>
<html lang="en">
<head>
<meta charset="utf-8">
<title>Corvel Athletic Hub – Teamwear Price List</title>
<link href="https://fonts.googleapis.com/css2?family=Exo+2:ital,wght@1,900&family=Lato:wght@400;700;900&display=swap" rel="stylesheet">
<style>
:root{
  --red:#d71920;
  --black:#0d0d0d;
  --white:#ffffff;
  --grey:#d9d9d9;
  --stage:#b9bbd3;
  --text:#222222;
}
*{box-sizing:border-box;margin:0;padding:0}
html,body{width:1200px;height:1200px;overflow:hidden}
body{background:var(--stage);font-family:"Lato",sans-serif;color:var(--text);position:relative}
.stage-label{position:absolute;top:18px;left:0;width:1200px;text-align:center;color:var(--white);font-size:38px;font-weight:400;letter-spacing:1px}
.page{position:absolute;top:158px;width:581px;height:822px;background:var(--white);overflow:hidden}
.page--one{left:15px}
.page--two{left:605px}
.masthead{position:absolute;top:0;left:0;width:581px;height:86px}
.masthead svg{position:absolute;inset:0}
.brand{position:absolute;left:30px;top:24px;display:flex;align-items:center;gap:8px;color:var(--black);font-weight:900;font-size:32px;letter-spacing:1px}
.brand-dot{width:18px;height:18px;border-radius:50%;background:var(--white)}
.contact{position:absolute;left:366px;top:17px;color:var(--white);font-size:11px;line-height:14px}
.contact li{list-style:none;display:flex;align-items:center;gap:6px}
.contact li:first-child{padding-left:0}
.contact .icon{width:9px;height:9px;border-radius:50%;background:var(--red);display:inline-block;flex:none}
.title-band{position:absolute;top:91px;left:0;width:581px;height:31px}
.title-band svg{position:absolute;inset:0}
.title-band h1{position:absolute;left:0;width:581px;top:-1px;text-align:center;font-family:"Exo 2",sans-serif;font-style:italic;font-weight:900;font-size:29px;color:var(--white);letter-spacing:1px}
.terms{position:absolute;top:122px;left:0;width:581px;height:35px;background:var(--grey);text-align:center;font-size:10px;line-height:13px;padding-top:4px}
.section-head{position:absolute;top:178px;left:20px;display:flex;align-items:center;gap:4px;font-family:"Exo 2",sans-serif;font-style:italic;font-weight:900;font-size:25px;color:var(--red)}
.section-head::before{content:"";border-left:16px solid var(--red);border-top:10px solid transparent;border-bottom:10px solid transparent}
.section-rule{position:absolute;top:207px;left:20px;width:230px;height:2px;background:var(--red)}
.item{position:absolute;width:130px;height:170px;border-left:2px solid var(--red);border-right:2px solid var(--red)}
.item::after{content:"";position:absolute;left:-2px;right:-2px;bottom:0;height:40px;background:linear-gradient(rgba(255,255,255,0),var(--white))}
.item-head{background:var(--red);color:var(--white);text-align:center;font-size:10px;line-height:12.5px;height:34px;display:flex;flex-direction:column;justify-content:center;margin:0 -2px}
.item-head strong{font-weight:400;text-transform:uppercase}
.item-photo{display:block;width:96px;height:96px;margin:8px auto 0;border-radius:3px}
.price{position:absolute;left:0;right:0;bottom:16px;text-align:center;color:var(--red);font-weight:900;font-size:16px;z-index:1}
.price small{font-size:10px}
.note{position:absolute;left:0;right:0;bottom:2px;text-align:center;font-size:7.5px;z-index:1}
.c1{left:18px}.c2{left:157px}.c3{left:294px}.c4{left:432px}
.r1{top:221px}.r2{top:404px}.r3{top:590px}
.feature-photo{position:absolute;left:336px;top:176px;width:236px;height:220px;background:radial-gradient(circle at 45% 45%,#9a9ca3,#d8d8da 70%,#ffffff)}
.addons{position:absolute;left:444px;top:281px;width:108px;height:108px;border-radius:50%;background:var(--black);color:var(--white);font-size:8px;line-height:10.5px;padding:18px 0 0 20px}
.addons h3{color:var(--red);font-size:9.5px;line-height:11px;text-align:center;margin-left:-20px;font-weight:900}
.addons li{list-style:none}
.addons li::before{content:"• ";color:var(--red)}
.foot-rule{position:absolute;left:0;top:768px;width:581px;height:3px;background:var(--black)}
.footer{position:absolute;left:0;top:774px;width:581px;height:48px;background:linear-gradient(90deg,var(--black),var(--red) 35%,var(--red));color:var(--white);text-align:center}
.footer p{font-size:9.5px;padding-top:6px}
.footer .url{font-size:14px;padding-top:4px}
.page--two .footer .url{font-size:17px;padding-top:14px}
</style>
</head>
<body>
<div class="stage-label">PAGE 1 &amp; 2</div>

<!-- Page one -->
<section class="page page--one">
  <header class="masthead">
    <svg width="581" height="86" viewBox="0 0 581 86"><rect width="581" height="86" fill="#0d0d0d"/><polygon points="0,0 294,0 240,86 0,86" fill="#d71920"/></svg>
    <div class="brand"><span class="brand-dot"></span>CORVEL</div>
    <ul class="contact">
      <li>Please contact us for an official quote:</li>
      <li><span class="icon"></span>03 5550 1274</li>
      <li><span class="icon"></span>marcus@corvelathletichub.com.au</li>
      <li><span class="icon"></span>www.corvelathletichub.com.au</li>
    </ul>
  </header>
  <div class="title-band">
    <svg width="581" height="31" viewBox="0 0 581 31"><rect width="581" height="31" fill="#0d0d0d"/><polygon points="300,0 581,0 581,31 285,31" fill="#d71920"/></svg>
    <h1>TEAMWEAR PRICE LIST</h1>
  </div>
  <p class="terms">Prices shown below exclude GST, Custom Clothing is based on order of 20 + units,<br>smaller order quantities are available on request</p>
  <h2 class="section-head">UNIFORMS</h2>
  <div class="section-rule"></div>

  <div class="feature-photo" role="img" aria-label="Athlete in grey compression top holding dumbbells"></div>
  <div class="addons">
    <h3>ADD ON<br>SERVICES</h3>
    <ul><li>Embroidery</li><li>Screen printing</li><li>Digital transfers</li><li>Names &amp; Numbers</li></ul>
  </div>

  <article class="item c1 r1"><div class="item-head"><strong>1 Club Polos</strong><span>with 1 logo embroidered</span></div><div class="item-photo" role="img" aria-label="Navy club polo" style="background:#1d2233"></div><div class="price">$21</div><div class="note">Huge range of colours and styles</div></article>
  <article class="item c2 r1"><div class="item-head"><strong>Fleece Hoodie</strong><span>with 1 logo embroidered</span></div><div class="item-photo" role="img" aria-label="Models in fleece hoodies" style="background:linear-gradient(90deg,#1f2536 50%,#8a8c92 50%)"></div><div class="price">$29</div></article>

  <article class="item c1 r2"><div class="item-head"><strong>Sublimated Polos</strong><span>Unlimited logos</span></div><div class="item-photo" role="img" aria-label="Black sublimated polo" style="background:#1a1a1a"></div><div class="price">$36</div></article>
  <article class="item c2 r2"><div class="item-head"><strong>Sublimated T Shirts</strong><span>Unlimited logos</span></div><div class="item-photo" role="img" aria-label="Red and black sublimated t-shirt" style="background:linear-gradient(#e02a2a,#2a1a1a)"></div><div class="price">$35</div></article>
  <article class="item c3 r2"><div class="item-head"><strong>Sublimated Singlets</strong><span>Unlimited logos</span></div><div class="item-photo" role="img" aria-label="Red, navy and yellow sublimated singlets" style="background:linear-gradient(135deg,#c4202a,#2a2f6a 50%,#f0c020)"></div><div class="price">$31</div></article>
  <article class="item c4 r2"><div class="item-head"><strong>Sublimated Hoodies</strong><span>Unlimited logos</span></div><div class="item-photo" role="img" aria-label="Red and black sublimated hoodie" style="background:linear-gradient(#d42a22,#1a1a1a)"></div><div class="price">$59</div></article>

  <article class="item c1 r3"><div class="item-head"><strong>Walk Out Shorts</strong><span>with 1 logo embroidered</span></div><div class="item-photo" role="img" aria-label="Black walk out shorts" style="background:linear-gradient(#2f6fb8 40%,#141414 40%)"></div><div class="price">$22</div></article>
  <article class="item c2 r3"><div class="item-head"><strong>Microfibre Track Pants</strong><span>with 1 logo embroidered</span></div><div class="item-photo" role="img" aria-label="Black microfibre track pants" style="background:#151515"></div><div class="price">$36</div></article>
  <article class="item c3 r3"><div class="item-head"><strong>Tappered Leg Fleecy<br>Track Pants</strong><span>with 1 logo embroidered</span></div><div class="item-photo" role="img" aria-label="Grey fleecy track pants" style="background:#cfcfd1"></div><div class="price">$39</div></article>
  <article class="item c4 r3"><div class="item-head"><strong>Softshell<br>Hooded Jackets</strong><span>with 1 logo embroidered</span></div><div class="item-photo" role="img" aria-label="Navy softshell hooded jacket" style="background:#1c2130"></div><div class="price">$75</div></article>

  <div class="foot-rule"></div>
  <footer class="footer">
    <p>View our full range catalogues&nbsp; look at stock "design your own" sublimated garments, etc. from our website:</p>
    <p class="url">www.corvelathletichub.com.au</p>
  </footer>
</section>

<!-- Page two -->
<section class="page page--two">
  <header class="masthead">
    <svg width="581" height="86" viewBox="0 0 581 86"><rect width="581" height="86" fill="#0d0d0d"/><polygon points="0,0 294,0 240,86 0,86" fill="#d71920"/></svg>
    <div class="brand"><span class="brand-dot"></span>CORVEL</div>
    <ul class="contact">
      <li>Please contact us for an official quote:</li>
      <li><span class="icon"></span>03 5550 1274</li>
      <li><span class="icon"></span>marcus@corvelathletichub.com.au</li>
      <li><span class="icon"></span>www.corvelathletichub.com.au</li>
    </ul>
  </header>
  <div class="title-band">
    <svg width="581" height="31" viewBox="0 0 581 31"><rect width="581" height="31" fill="#0d0d0d"/><polygon points="300,0 581,0 581,31 285,31" fill="#d71920"/></svg>
    <h1>TEAMWEAR PRICE LIST</h1>
  </div>
  <p class="terms">Prices shown below exclude GST, Custom Clothing is based on order of 20 + units,<br>smaller order quantities are available on request</p>
  <h2 class="section-head">UNIFORMS</h2>
  <div class="section-rule"></div>

  <article class="item c1 r1"><div class="item-head"><strong>Softshell Jackets</strong><span>with 1 logo embroidered</span></div><div class="item-photo" role="img" aria-label="Models in navy softshell jackets" style="background:linear-gradient(90deg,#1d2536,#3a4256)"></div><div class="price">$52</div></article>
  <article class="item c2 r1"><div class="item-head"><strong>Softshell Vests</strong><span>with 1 logo embroidered</span></div><div class="item-photo" role="img" aria-label="Grey softshell vest" style="background:linear-gradient(#5cc08a 30%,#3b3f4c 30%)"></div><div class="price">$45</div></article>
  <article class="item c3 r1"><div class="item-head"><strong>AFL Jumpers</strong><span>Your design with logos</span></div><div class="item-photo" role="img" aria-label="Blue and grey AFL jumpers" style="background:linear-gradient(#2a2fb0 40%,#b0b4c4 40%,#b0b4c4 52%,#2a2fb0 52%)"></div><div class="price">$36</div></article>
  <article class="item c4 r1"><div class="item-head"><strong>AFL Shorts</strong><span>Your design with all logos</span></div><div class="item-photo" role="img" aria-label="Blue AFL shorts" style="background:#2a32b8"></div><div class="price">$22<small>.90</small></div></article>

  <article class="item c1 r2"><div class="item-head"><strong>Aline Netball Dress</strong><span>Your design with all logos</span></div><div class="item-photo" role="img" aria-label="Light blue netball dress" style="background:linear-gradient(#8fc3e8,#bfe0f2)"></div><div class="price">$49</div></article>
  <article class="item c2 r2"><div class="item-head"><strong>Elite Netballdress<br>Speed Back</strong><span>Your design with logos</span></div><div class="item-photo" role="img" aria-label="Green and gold netball dresses" style="background:linear-gradient(135deg,#1a4a2a,#2a6a3a 60%,#e8d040)"></div><div class="price">$69</div></article>
  <article class="item c3 r2"><div class="item-head"><strong>Netball Bib Set</strong><span>Sublimated to<br>match dress</span></div><div class="item-photo" role="img" aria-label="Black netball bibs with pink position letters" style="background:#222"></div><div class="price">$75</div></article>
  <article class="item c4 r2"><div class="item-head"><strong>Basketball Singlets</strong><span>Your design with all logos</span></div><div class="item-photo" role="img" aria-label="Grey and blue basketball singlets" style="background:linear-gradient(90deg,#c0c2c8 50%,#2a30a8 50%)"></div><div class="price">$31</div></article>

  <article class="item c1 r3"><div class="item-head"><strong>Basketball Shorts</strong><span>Your design with all logos</span></div><div class="item-photo" role="img" aria-label="Grey basketball shorts with blue panels" style="background:#c6c8ce"></div><div class="price">$25</div></article>
  <article class="item c2 r3"><div class="item-head"><strong>Soccer Shirts</strong><span>Your design with all logos</span></div><div class="item-photo" role="img" aria-label="Blue and white striped soccer shirts" style="background:repeating-linear-gradient(90deg,#2a30b0 0 12px,#ffffff 12px 20px)"></div><div class="price">$35</div></article>
  <article class="item c3 r3"><div class="item-head"><strong>Soccer Shorts</strong><span>Your design with all logos</span></div><div class="item-photo" role="img" aria-label="Blue soccer shorts" style="background:#2a32b8"></div><div class="price">$25</div></article>
  <article class="item c4 r3"><div class="item-head"><strong>Cricket V Neck Shirts</strong><span>Unlimited Logos</span></div><div class="item-photo" role="img" aria-label="Blue and grey cricket shirts" style="background:linear-gradient(#2a2fb0 45%,#b8bac6 45%,#b8bac6 60%,#2a2fb0 60%)"></div><div class="price">$35</div></article>

  <div class="foot-rule"></div>
  <footer class="footer">
    <p class="url">www.corvelathletichub.com.au</p>
  </footer>
</section>
</body>
</html>
```